MRT Property - Business Cards

Looking for a business card & general letterhead, signage etc design for our new logo.

Colours:
000a20
0056a2
00b5ef
0088ce
68cef2

Fonts:
Poppins
Karla

Please keep look and feel of new brand - example in the zip package I sent.

```html
<!DOCTYPE html>
<html lang="en">
<head>
<meta charset="utf-8">
<title>MRT Property – Business Cards</title>
<link href="https://fonts.googleapis.com/css2?family=Poppins:wght@400;500;600;700&display=swap" rel="stylesheet">
<style>
  :root {
    --ink: #000a20;
    --navy-card: #1b1f36;
    --brand-blue: #0056a2;
    --sky: #00b5ef;
    --mid-blue: #0088ce;
    --pale-blue: #68cef2;
    --paper: #fbfbfb;
    --stage: #e9ebef;
    --text-dark: #1a1a1a;
    --text-soft: #4a4a4a;
  }
  * { box-sizing: border-box; margin: 0; padding: 0; }
  html, body {
    width: 1200px; height: 852px; overflow: hidden;
    background: var(--stage);
    font-family: "Poppins", sans-serif;
  }
  .stage {
    position: relative; width: 1200px; height: 852px;
  }
  .card {
    position: absolute; top: 276px;
    width: 525px; height: 300px;
    border-radius: 18px; overflow: hidden;
    box-shadow: 0 10px 28px rgba(0, 10, 32, 0.18);
  }

  /* Back of card */
  .card--back { left: 50px; background: var(--navy-card); }
  .card--back .brand-name {
    position: absolute; left: 0; right: 0; top: 104px;
    text-align: center; font-weight: 700; font-size: 44px;
    color: var(--brand-blue); letter-spacing: 0.5px;
  }
  .card--back .website {
    position: absolute; right: 40px; bottom: 42px;
    font-size: 11px; letter-spacing: 6px; color: #c9ccd8;
  }
  .card--back .rule {
    position: absolute; left: 40px; right: 40px; bottom: 28px; height: 4px;
    background: linear-gradient(90deg, var(--mid-blue) 0 60%, var(--sky) 60% 100%);
  }

  /* Front of card */
  .card--front { left: 625px; background: var(--paper); }
  .card--front .brand-name {
    position: absolute; right: 36px; top: 54px;
    font-weight: 700; font-size: 30px; color: var(--brand-blue);
  }
  .person { position: absolute; left: 34px; top: 150px; }
  .person__name { font-weight: 600; font-size: 20px; color: var(--text-dark); line-height: 1.1; }
  .person__role { font-size: 10.5px; color: var(--text-soft); margin-top: 2px; }
  .contacts { position: absolute; left: 34px; top: 206px; list-style: none; }
  .contacts li {
    display: flex; align-items: center; gap: 12px;
    font-size: 12.5px; color: var(--text-dark); height: 20px;
  }
  .contacts svg { width: 12px; height: 12px; fill: var(--mid-blue); }
  .address-band {
    position: absolute; right: 0; bottom: 44px; width: 265px; height: 48px;
    background: var(--brand-blue); border-top-left-radius: 22px;
    display: flex; align-items: center; justify-content: flex-end; padding-right: 22px;
    font-size: 11.5px; color: #ffffff; letter-spacing: 0.2px;
  }
  .accent-strip {
    position: absolute; left: 0; right: 0; bottom: 0; height: 44px;
    background: var(--sky);
    clip-path: polygon(0 70%, 50% 0, 100% 0, 100% 100%, 0 100%);
  }
  .accent-strip::after {
    content: ""; position: absolute; left: 0; right: 0; bottom: 0; height: 22px;
    background: var(--paper);
    clip-path: polygon(0 100%, 0 60%, 50% 0, 100% 0, 100% 100%);
  }
</style>
</head>
<body>
<main class="stage">
  <section class="card card--back" aria-label="Card back">
    <div class="brand-name">MRT Property</div>
    <div class="website">www.mrtproperty.com</div>
    <div class="rule"></div>
  </section>

  <section class="card card--front" aria-label="Card front">
    <div class="brand-name">MRT Property</div>

    <div class="person">
      <div class="person__name">Callum Reid</div>
      <div class="person__role">Associate Director</div>
    </div>

    <ul class="contacts">
      <li>
        <svg viewBox="0 0 24 24" aria-hidden="true"><path d="M6.6 10.8a15 15 0 0 0 6.6 6.6l2.2-2.2a1 1 0 0 1 1-.25 11.4 11.4 0 0 0 3.6.6 1 1 0 0 1 1 1V20a1 1 0 0 1-1 1A17 17 0 0 1 3 4a1 1 0 0 1 1-1h3.5a1 1 0 0 1 1 1c0 1.25.2 2.45.6 3.6a1 1 0 0 1-.25 1z"/></svg>
        555-010-0199
      </li>
      <li>
        <svg viewBox="0 0 24 24" aria-hidden="true"><path d="M2 5h20v14H2z M2 5l10 8 10-8" /></svg>
        callum@mrtproperty.com
      </li>
      <li>
        <svg viewBox="0 0 24 24" aria-hidden="true"><circle cx="12" cy="12" r="10"/></svg>
        www.mrtproperty.com
      </li>
    </ul>

    <div class="accent-strip"></div>
    <div class="address-band">52 Harbour View Road Northmead</div>
  </section>
</main>
</body>
</html>
```